Harbor Law Stationary - Law Firm

I am looking for a designer who can help me design letterhead and envelopes consistent with our new business cards. Feel free to reach out to me directly at ned@harborlawgroup.example. Thank you!! Visit harborlawgroup.example to see our site and the attached files for creative assets.

Target Market(s)

Anyone needing a lawyer

Font styles to use
Other font styles liked:
• Adobe Caslon Pro

Requirements
Must have
• Adobe Caslon Pro font
Full color
Nice to have
• My photo on front along with 2/3 face of camo - see mock up for example of what I have in mind.

American colors - similar to the ones found on my website and gold.

```html
<!DOCTYPE html>
<html lang="en">
<head>
<meta charset="utf-8">
<title>Harbor Law — Letterhead</title>
<link rel="stylesheet" href="https://fonts.googleapis.com/css2?family=Libre+Caslon+Text:wght@400;700&family=Open+Sans:wght@400&display=swap">
<style>
  :root {
    --backdrop: #dcdcdc;
    --paper: #f7f7f7;
    --navy: #0c2444;
    --ink: #4a4a4a;
    --white: #ffffff;
    --signature-tone: #e6e6e6;
  }
  * { box-sizing: border-box; margin: 0; padding: 0; }
  html, body {
    width: 1153px;
    height: 1200px;
    overflow: hidden;
    background: var(--backdrop);
  }
  .letterhead {
    position: absolute;
    left: 161px;
    top: 20px;
    width: 831px;
    height: 1160px;
    background: var(--paper);
  }
  .masthead {
    position: absolute;
    left: 0; top: 0;
    width: 100%;
    height: 169px;
    background: var(--navy);
  }
  .firm-name {
    position: absolute;
    left: 74px;
    top: 68px;
    font-family: "Libre Caslon Text", serif;
    font-weight: 400;
    font-size: 24px;
    line-height: 30px;
    color: var(--white);
    white-space: nowrap;
  }
  .contact {
    position: absolute;
    right: 60px;
    top: 32px;
    font-family: "Libre Caslon Text", serif;
    font-size: 14px;
    line-height: 18px;
    color: var(--white);
    font-style: normal;
  }
  .contact .address { margin-bottom: 6px; }
  .letter-body {
    position: absolute;
    left: 74px;
    top: 291px;
    width: 682px;
    font-family: "Open Sans", sans-serif;
    font-size: 14.9px;
    line-height: 22.3px;
    color: var(--ink);
  }
  .letter-body p {
    text-align: justify;
    margin-bottom: 22.5px;
  }
  .signature {
    position: absolute;
    left: 76px;
    top: 878px;
    width: 98px;
    height: 92px;
    background: var(--signature-tone);
    border-radius: 4px;
  }
  .practice-band {
    position: absolute;
    left: 0; bottom: 0;
    width: 100%;
    height: 54px;
    background: var(--navy);
    display: flex;
    justify-content: center;
    align-items: center;
    gap: 10px;
    font-family: "Libre Caslon Text", serif;
    font-size: 18px;
    color: var(--white);
    list-style: none;
  }
  .practice-band li::before {
    content: "";
    display: inline-block;
    width: 8px;
    height: 8px;
    border-radius: 50%;
    background: var(--white);
    margin-right: 7px;
    vertical-align: middle;
    position: relative;
    top: -2px;
  }
</style>
</head>
<body>
  <main class="letterhead">
    <header class="masthead">
      <div class="firm-name">Harbor Law</div>
      <address class="contact">
        <div class="address">48 Wharf Row<br>Port Haven, ME 04101</div>
        <div>(555) 010-2290<br>ned@harborlawgroup.example<br>www.harborlawgroup.example</div>
      </address>
    </header>

    <section class="letter-body">
      <p class="salutation">Dear customer,</p>
      <p>Lorem ipsum dolor sit amet, consectetur adipisicing elit, sed do eiusmod tempor incididunt ut labore et dolore magna aliqua. Ut enim ad minim veniam, quis nostrud exercitation ullamco laboris nisi ut aliquip ex ea commodo consequat. Duis aute irure dolor in reprehenderit in voluptate velit esse cillum dolore eu fugiat nulla pariatur. Excepteur sint occaecat cupidatat non proident, sunt in culpa qui officia deserunt mollit anim id est laborum.</p>
      <p>Lorem ipsum dolor sit amet, consectetur adipisicing elit, sed do eiusmod tempor incididunt ut labore et dolore magna aliqua. Ut enim ad minim veniam, quis nostrud exercitation ullamco laboris nisi ut aliquip ex ea commodo consequat. Duis aute irure dolor in reprehenderit in voluptate velit esse cillum dolore eu fugiat nulla pariatur. Excepteur sint occaecat cupidatat non proident, sunt in culpa qui officia deserunt mollit anim id est laborum.</p>
      <p>Lorem ipsum dolor sit amet, consectetur adipisicing elit, sed do eiusmod tempor incididunt ut labore et dolore magna aliqua. Ut enim ad minim veniam, quis nostrud exercitation ullamco laboris nisi ut aliquip ex ea commodo consequat. Duis aute irure dolor in reprehenderit in voluptate velit esse cillum dolore eu fugiat nulla pariatur. Excepteur sint occaecat cupidatat non proident, sunt in culpa qui officia deserunt mollit anim id est laborum.</p>
      <p>Lorem ipsum dolor sit amet, consectetur adipisicing elit, sed do eiusmod tempor incididunt ut labore et dolore magna aliqua. Ut enim ad minim veniam, quis nostrud exercitation ullamco laboris nisi ut aliquip ex ea commodo consequat. Duis aute irure dolor in reprehenderit.</p>
      <p class="closing">Yours Sincerely,</p>
    </section>

    <div class="signature" role="img" aria-label="Handwritten signature of the sender"></div>

    <ul class="practice-band">
      <li>Personal Injury</li>
      <li>Injunctions</li>
      <li>Criminal Defense</li>
      <li>Family Law</li>
    </ul>
  </main>
</body>
</html>
```